Book cover design for a collection of poetry - The Lanternfield

Book cover and back design need to be moody, nostalgic, reflective, ethereal. Melancholy and other worldly. Cover design should not be time specific to a period or place but if applicable should reflect British landscape. Book cover should be in tones of blue and must include the title and author (THE LANTERNFIELD BY CORBIN WHITLACE). We love the idea of rain, and looking out of a window. See attached designs. A world you are observing but not in.

Industry/Entity Type

Book Publisher

Font styles to use
Serif
Script

Colors
3176b5
3377b5
85acd3
eaf1f7
0792cd
33a6d7
86cae7
ecf7fb
86cfc6

Requirements
Must have
• The colour blue in it, must be melancholy and reflective.
Nice to have
• Rain in the cover.
Should not have
• Any bright colours.

```html
<!DOCTYPE html>
<html lang="en">
<head>
<meta charset="utf-8">
<title>The Lanternfield — Cover Wrap</title>
<link href="https://fonts.googleapis.com/css2?family=Questrial&display=swap" rel="stylesheet">
<style>
  :root {
    --page-bg: #f1f2f3;
    --sky-top: #7696b4;
    --sky-mid: #5f7f9f;
    --cloud-band: #4e6c8c;
    --horizon: #3a536e;
    --land: #18212c;
    --land-deep: #0f151d;
    --ink-light: #eaf1f7;
  }
  * { box-sizing: border-box; margin: 0; padding: 0; }
  html, body {
    width: 1200px;
    height: 800px;
    overflow: hidden;
    background: var(--page-bg);
  }
  .canvas {
    position: relative;
    width: 1200px;
    height: 800px;
  }
  .cover-wrap {
    position: absolute;
    left: 82px;
    top: 20px;
    width: 1036px;
    height: 761px;
    overflow: hidden;
    color: var(--ink-light);
    font-family: "Questrial", sans-serif;
    box-shadow: 0 2px 6px rgba(0,0,0,0.12);
  }
  .rain-window-scene {
    position: absolute;
    inset: 0;
    background: linear-gradient(
      to bottom,
      var(--sky-top) 0%,
      var(--sky-mid) 18%,
      var(--cloud-band) 34%,
      var(--sky-mid) 52%,
      var(--horizon) 70%,
      var(--land) 78%,
      var(--land-deep) 100%
    );
  }
  .back-panel {
    position: absolute;
    left: 0;
    top: 0;
    width: 516px;
    height: 100%;
    text-align: center;
    text-transform: uppercase;
  }
  .back-heading {
    position: absolute;
    top: 50px;
    left: 0;
    width: 516px;
    font-size: 15px;
    letter-spacing: 8px;
    line-height: 31.5px;
  }
  .back-blurb {
    position: absolute;
    left: 0;
    width: 516px;
    font-size: 13px;
    letter-spacing: 4.3px;
    line-height: 21px;
  }
  .blurb-part-one { top: 196px; }
  .blurb-part-two { top: 408px; }
  .spine {
    position: absolute;
    left: 500px;
    top: 0;
    width: 44px;
    height: 100%;
  }
  .spine-title {
    position: absolute;
    left: 7px;
    top: 112px;
    writing-mode: vertical-rl;
    font-size: 27px;
    letter-spacing: 2px;
    white-space: nowrap;
  }
  .spine-author {
    position: absolute;
    left: 16px;
    top: 432px;
    writing-mode: vertical-rl;
    font-size: 9px;
    letter-spacing: 0.6px;
    white-space: nowrap;
  }
  .front-panel {
    position: absolute;
    left: 544px;
    top: 0;
    width: 492px;
    height: 100%;
    text-align: center;
  }
  .front-title {
    position: absolute;
    top: 140px;
    left: 0;
    width: 492px;
    font-size: 52px;
    font-weight: 400;
    letter-spacing: 1px;
    line-height: 82px;
  }
  .front-author {
    position: absolute;
    top: 656px;
    left: 0;
    width: 492px;
    font-size: 21px;
    letter-spacing: 1.6px;
  }
</style>
</head>
<body>
  <main class="canvas">
    <section class="cover-wrap">
      <div class="rain-window-scene" role="img" aria-label="Photograph of rain drops on a window pane, looking out over a grey-blue clouded sky and a dark distant landscape"></div>

      <div class="back-panel">
        <p class="back-heading">TheLanternfield<br>isa<br>collectionofpoetry</p>
        <p class="back-blurb blurb-part-one">
          toldintwopartswefirstmeetcharles-<br>
          aged,crippledandleftaloneinhis<br>
          inheritedmarshhouse-reflectingonhis<br>
          lifeandhismarriagetobeautifulalice<br>
          whowemeetinparttwo.aliceissuicidal,<br>
          manicallydepressedandstrugglingwith<br>
          lifeasawifeandmother.shemeets,<br>
          harborsandfallsinlovewithasoldier<br>
          duringwwiiandherworldischangedforever.
        </p>
        <p class="back-blurb blurb-part-two">
          movingthroughthe20thcentury,thislife<br>
          andthenext,thelanternfieldinterweaves<br>
          grief,loss,theafter-life,mentalillness,<br>
          andultimatelythetruenatureoflove.
        </p>
      </div>

      <div class="spine">
        <h2 class="spine-title">THE LANTERNFIELD</h2>
        <p class="spine-author">BY CORBIN WHITLACE</p>
      </div>

      <div class="front-panel">
        <h1 class="front-title">THE<br>LANTERNFIELD</h1>
        <p class="front-author">BY CORBIN WHITLACE</p>
      </div>
    </section>
  </main>
</body>
</html>
```